Investment Management Firm Power point template

Marrow Holdings is a real estate investment firm focused on buying commercial office and residential property in the UK. We produce powerpoint presentations for our Board of Directors, Investment Committee and also to external investors.

We are looking for a powerpoint design template which we can use for future presentations which provide a professional look and feel.

Our current website: http://www.marrowholdings.example.co.uk/

Target Market(s)

Institution Investors, Board of Directors, Professionals

Industry/Entity Type

Real Estate

Requirements
Must have
• Leverage off the current logo and colour scheme. However, does not have to purely rely on this colour scheme.
• - Title page
• - Content Page
• - Slide where graphs can be incorporated
• - Slide where photos can be incorporated
• - Slide of UK Map which can show where the property portfolio is currently located
• - Other slides incorporating smart art or other designs that can be used for future presentations
Nice to have
• An example of graphics that we would love to have in the powerpoint pack which we can easily edit has been attached

```html
<!DOCTYPE html>
<html lang="en">
<head>
<meta charset="utf-8">
<title>Marrow Holdings – Team Slide</title>
<link href="https://fonts.googleapis.com/css2?family=Arimo:wght@400;500;600&family=Tenor+Sans&display=swap" rel="stylesheet">
<style>
  :root {
    --page-bg: #ffffff;
    --ink: #111111;
    --brand-grey: #3a3a3a;
    --brand-blue: #2f5575;
    --teal-dark: #1f3d47;
    --teal-mid: #3f6b74;
    --teal-light: #7fa3a6;
    --panel: #ffffff;
    --corner-dark: #1c1d20;
    --frame-line: #3e5d80;
    --photo-light: #dfe5ee;
    --photo-mid: #8a9fb8;
    --photo-dark: #2b3e5a;
  }
  * { box-sizing: border-box; margin: 0; padding: 0; }
  html, body {
    width: 1200px; height: 1000px; overflow: hidden;
    background: var(--page-bg);
    font-family: "Arimo", Arial, sans-serif;
  }
  .board { position: relative; width: 1200px; height: 1000px; }
  .board-title {
    position: absolute; top: 112px; left: 0; width: 1200px;
    text-align: center;
    font-family: "Tenor Sans", sans-serif;
    font-size: 27px; color: var(--ink); font-weight: 400;
  }
  .slide {
    position: absolute; left: 134px; top: 175px; width: 946px; height: 709px;
    overflow: hidden;
    border: 1px solid #b9c3cf;
    background:
      radial-gradient(ellipse at 75% 85%, var(--teal-light) 0%, transparent 45%),
      radial-gradient(ellipse at 15% 60%, #5d878d 0%, transparent 50%),
      linear-gradient(160deg, var(--teal-dark) 0%, var(--teal-mid) 55%, #2a4f58 100%);
  }
  .slide-texture { position: absolute; inset: 0; }
  .corner-white {
    position: absolute; left: 0; top: 0; width: 136px; height: 93px;
    background: var(--panel);
  }
  .edge-dark {
    position: absolute; right: 0; top: 0; width: 40px; height: 140px;
    background: linear-gradient(180deg, var(--corner-dark) 0%, rgba(28,29,32,0) 100%);
  }
  .content-panel {
    position: absolute; left: 136px; top: 0; width: 770px; height: 628px;
    background: linear-gradient(180deg, rgba(255,255,255,1) 0%, rgba(255,255,255,0.97) 25%, rgba(240,242,243,0.85) 60%, rgba(225,230,232,0.72) 100%);
    box-shadow: -6px 6px 14px rgba(0,0,0,0.25);
  }
  .corner-fold { position: absolute; left: 120px; top: 578px; }
  .brand {
    position: absolute; left: 147px; top: 37px;
    display: flex; align-items: center; gap: 12px;
  }
  .brand-square { width: 54px; height: 55px; background: var(--brand-blue); }
  .brand-name {
    font-family: "Arimo", Arial, sans-serif; font-weight: 400;
    font-size: 42px; color: var(--brand-grey); letter-spacing: -0.5px;
  }
  .section-title {
    position: absolute; left: 208px; top: 137px;
    font-size: 21px; font-weight: 500; color: var(--ink);
  }
  .member { position: absolute; top: 190px; width: 194px; }
  .member-1 { left: 173px; }
  .member-2 { left: 412px; }
  .member-3 { left: 651px; }
  .member-photo {
    width: 194px; height: 205px;
    background: linear-gradient(180deg, var(--photo-light) 0%, var(--photo-mid) 60%, var(--photo-dark) 100%);
    box-shadow: 8px 6px 10px rgba(0,0,0,0.25);
  }
  .member-name {
    margin: 13px auto 0; width: 134px; height: 28px;
    border: 1px solid var(--frame-line);
    background: rgba(255,255,255,0.6);
    text-align: center; line-height: 26px;
    font-size: 14px; color: var(--ink);
  }
  .member-bio {
    margin: 20px -10px 0; text-align: center;
    font-size: 13.4px; line-height: 17.5px; color: var(--ink);
  }
</style>
</head>
<body>
<div class="board">
  <h1 class="board-title">Power point Content with pictures</h1>

  <div class="slide">
    <svg class="slide-texture" width="946" height="709" aria-hidden="true">
      <path d="M0 440 C 80 420, 120 470, 136 520" stroke="rgba(255,255,255,0.12)" stroke-width="2" fill="none"/>
      <path d="M500 690 C 560 660, 640 700, 700 670" stroke="rgba(0,0,0,0.15)" stroke-width="1.5" fill="none"/>
    </svg>
    <div class="corner-white"></div>
    <div class="edge-dark"></div>

    <div class="content-panel"></div>
    <svg class="corner-fold" width="60" height="61" aria-hidden="true">
      <polygon points="0,0 0,61 60,61" fill="var(--corner-dark)"/>
    </svg>

    <div class="brand">
      <div class="brand-square"></div>
      <span class="brand-name">Marrow Holdings</span>
    </div>

    <h2 class="section-title">THE TEAM</h2>

    <div class="member member-1">
      <div class="member-photo" role="img" aria-label="Portrait photo of Ravi in a dark suit"></div>
      <div class="member-name">Ravi</div>
      <p class="member-bio">Lorem ipsum dolor sit amet, consectetuer adipiscing elit. Aenean commodo ligula eget dolor. Aenean massa. Cum sociis natoque penatibus et magnis dis parturient montes, nascetur.</p>
    </div>

    <div class="member member-2">
      <div class="member-photo" role="img" aria-label="Portrait photo of Lukas in a blazer and open shirt"></div>
      <div class="member-name">Lukas</div>
      <p class="member-bio">Lorem ipsum dolor sit amet, consectetuer adipiscing elit. Aenean commodo ligula eget dolor. Aenean massa. Cum sociis natoque penatibus et magnis dis parturient montes, nascetur.</p>
    </div>

    <div class="member member-3">
      <div class="member-photo" role="img" aria-label="Portrait photo of Felix in a knit sweater"></div>
      <div class="member-name">Felix</div>
      <p class="member-bio">Lorem ipsum dolor sit amet, consectetuer adipiscing elit. Aenean commodo ligula eget dolor. Aenean massa. Cum sociis natoque penatibus et magnis dis parturient montes, nascetur.</p>
    </div>
  </div>
</div>
</body>
</html>
```